business card design for a plumbing contractor

i need a double business card for a plumbing business, our initial service is residential Sewer Drain Cleaning.

Target Market(s)

other plumbing Business

Industry/Entity Type

Plumbing

Contact Information for Business Card

www.PipeworksTopMark.example- 5307218394-

Font styles to use
Serif

Colors
ec1f27
0455a3

```html
<!DOCTYPE html>
<html lang="en">
<head>
<meta charset="utf-8">
<title>Pipeworks Top Mark – Business Card</title>
<link rel="stylesheet" href="https://fonts.googleapis.com/css2?family=Roboto+Condensed:wght@400;700&display=swap">
<style>
  :root {
    --backdrop: #e9e6e1;
    --card: #ffffff;
    --ink: #5f5f5f;
    --ink-soft: #8a8a8a;
    --accent: #e5322d;
    --rule: #d6d6d6;
  }
  * { margin: 0; padding: 0; box-sizing: border-box; }
  html, body {
    width: 1200px; height: 886px; overflow: hidden;
    background: var(--backdrop);
    font-family: "Roboto Condensed", sans-serif;
  }
  .sheet {
    width: 1200px; height: 886px;
    display: flex; align-items: center; justify-content: center; gap: 40px;
  }
  .card {
    position: relative;
    width: 540px; height: 309px;
    background: var(--card);
    border-radius: 18px;
    box-shadow: 0 6px 18px rgba(0,0,0,.12);
  }
  /* front */
  .card-front .identity {
    position: absolute; left: 70px; top: 118px; width: 160px;
    text-align: right;
  }
  .identity .name {
    color: var(--accent); font-size: 25px; font-weight: 400;
    letter-spacing: .5px; text-transform: uppercase; line-height: 1.1;
  }
  .identity .title {
    color: var(--ink); font-size: 18px; text-transform: uppercase; line-height: 1.2;
  }
  .card-front .divider {
    position: absolute; left: 250px; top: 100px; width: 1px; height: 100px;
    background: var(--rule);
  }
  .contacts {
    position: absolute; left: 268px; top: 108px;
    list-style: none; font-size: 14.5px; color: var(--ink);
  }
  .contacts li { display: flex; align-items: center; gap: 8px; height: 27px; }
  .contacts svg { width: 13px; height: 13px; flex: none; }
  /* back */
  .card-back .brand {
    position: absolute; left: 0; right: 0; top: 128px;
    display: flex; align-items: center; justify-content: center; gap: 12px;
  }
  .brand .dot { width: 22px; height: 22px; border-radius: 50%; background: var(--accent); }
  .brand .brand-name { font-size: 40px; font-weight: 700; color: var(--ink); letter-spacing: .3px; }
  .service {
    position: absolute; font-size: 14px; color: var(--ink-soft);
  }
  .service-top { left: 34px; top: 30px; }
  .service-bottom { right: 34px; bottom: 30px; }
</style>
</head>
<body>
<main class="sheet">
  <section class="card card-front" aria-label="Card front">
    <div class="identity">
      <p class="name">Dana Rivers</p>
      <p class="title">CEO/Founder</p>
    </div>
    <div class="divider"></div>
    <ul class="contacts">
      <li>
        <svg viewBox="0 0 24 24" aria-hidden="true"><path fill="var(--accent)" d="M6.6 10.8a15 15 0 0 0 6.6 6.6l2.2-2.2c.3-.3.7-.4 1-.2 1.1.4 2.3.6 3.6.6.6 0 1 .4 1 1V20c0 .6-.4 1-1 1A17 17 0 0 1 3 4c0-.6.4-1 1-1h3.5c.6 0 1 .4 1 1 0 1.3.2 2.5.6 3.6.1.3 0 .7-.2 1z"/></svg>
        <span>5307218394</span>
      </li>
      <li>
        <svg viewBox="0 0 24 24" aria-hidden="true"><rect x="2" y="5" width="20" height="14" rx="2" fill="var(--accent)"/><path d="M3 6l9 7 9-7" stroke="#fff" stroke-width="2" fill="none"/></svg>
        <span>Dispatcher@PipeworksTopMark.example</span>
      </li>
      <li>
        <svg viewBox="0 0 24 24" aria-hidden="true"><circle cx="12" cy="12" r="10" fill="var(--accent)"/><path d="M2 12h20M12 2c3 3 3 17 0 20M12 2c-3 3-3 17 0 20" stroke="#fff" stroke-width="1.5" fill="none"/></svg>
        <span>www.PipeworksTopMark.example</span>
      </li>
    </ul>
  </section>

  <section class="card card-back" aria-label="Card back">
    <p class="service service-top">Sewer Drain Cleaning</p>
    <div class="brand">
      <span class="dot"></span>
      <span class="brand-name">Pipeworks Top Mark</span>
    </div>
    <p class="service service-bottom">Trenchless Pipe Installs</p>
  </section>
</main>
</body>
</html>
```